Brightway Haus Inc. Business Card Design

Brightway Haus Inc. is in search of a great clean design for our business cards!

Looking to incorporate our full logo and watermark on side one (however, I am open to having the text and watermark separated within the design.)

On side two, I am looking to have contact information (Name, Position, Phone #, Email, Website (www.thebrightwayhaus.ca). Can have the logo and/or watermark as part of the design if applicable.

Please add tagline "Where Shine Counts" on either side 1 or 2. This tagline can be in a sans serif, serif or cursive font as long as it compliments overall design. Capitalization can be title or sentence case depending on how it fits within the design.

Get creative!! Looking for a clean, crisp, premium design! Looking for a glossy card finish with spot UV features when printed. Cards will also be printed with rounded corners. Standard dimensions (3.5 x 2).

Target Market(s)

B2B - primary clients are business owners or property management corporations. (residential jobs are few and far between)

Industry/Entity Type

Business

Contact Information for Business Card

- clean, crisp design
- double sided
- spot UV accents and glossy finish upon printing
- standard business card size (3.5 x 2) with rounded corners
- please see project description for requirements per side

Font styles to use
Sans Serif

Requirements
Must have
• - adequate bleeds with print ready files
• - cohesive design elements between side 1 & 2
• - spot UV elements (can be on both sides or just one, use your discretion)
• - colour pallet should match the logo file provided
• - incorporate tagline "where shine counts" (this tagline can be in a serif or sans serif font as long as it is complimentary to the overall design.
Nice to have
• - Premium elements with a clean design
Should not have
• - Please omit cartoon or whimsical like designs, think premium.
• - Colours should not stray from the pallet of the provided logo.

```html
<!DOCTYPE html>
<html lang="en">
<head>
<meta charset="utf-8">
<title>Brightway Haus Inc. Business Cards</title>
<link href="https://fonts.googleapis.com/css2?family=Roboto:wght@400;500;700&display=swap" rel="stylesheet">
<style>
  :root {
    --teal: #23b9bd;
    --navy: #1d2a5e;
    --navy-deep: #18234f;
    --ink: #17191d;
    --white: #ffffff;
    --mist: #e9ebeb;
    --stage: #e4e4e2;
    --rule: #9a9ca0;
  }
  * { margin: 0; padding: 0; box-sizing: border-box; }
  html, body { width: 1200px; height: 769px; overflow: hidden; }
  body {
    background: var(--stage);
    font-family: "Roboto", Arial, sans-serif;
    position: relative;
  }
  .card {
    position: absolute;
    top: 230px;
    width: 540px;
    height: 309px;
    border-radius: 14px;
    overflow: hidden;
    box-shadow: 0 6px 18px rgba(0,0,0,0.18);
  }

  /* Contact side */
  .card--contact { left: 30px; background: var(--navy); }
  .watermark-area {
    position: absolute;
    inset: 0;
    clip-path: polygon(0 0, 56% 0, 36% 100%, 0 100%);
    background: linear-gradient(150deg, var(--teal) 0%, var(--teal) 45%, var(--mist) 100%);
  }
  .contact-block {
    position: absolute;
    right: 26px;
    top: 62px;
    text-align: right;
    color: var(--white);
    font-size: 13px;
    line-height: 17px;
  }
  .contact-name {
    color: var(--teal);
    font-size: 17px;
    font-weight: 500;
    letter-spacing: 0.2px;
    line-height: 20px;
  }
  .contact-role {
    font-weight: 700;
    font-size: 13.5px;
    margin-bottom: 10px;
  }
  .contact-address { margin-bottom: 6px; }
  .contact-line {
    display: flex;
    justify-content: flex-end;
    align-items: center;
    gap: 7px;
  }
  .contact-line svg { width: 11px; height: 11px; flex: none; }

  /* Brand side */
  .card--brand { left: 630px; background: var(--ink); }
  .brand-lockup {
    position: absolute;
    left: 0; right: 0;
    top: 118px;
    display: flex;
    justify-content: center;
    align-items: center;
    gap: 12px;
  }
  .brand-mark {
    width: 34px; height: 34px;
    background: var(--teal);
  }
  .brand-name {
    color: var(--teal);
    font-size: 33px;
    font-weight: 700;
    letter-spacing: 0.5px;
  }
  .tagline {
    position: absolute;
    left: 0; right: 0;
    top: 182px;
    display: flex;
    justify-content: center;
    align-items: center;
    gap: 8px;
    color: var(--white);
    font-size: 14px;
  }
  .tagline-rule {
    width: 120px;
    height: 1px;
    background: linear-gradient(90deg, transparent, var(--rule));
  }
  .tagline-rule--end { background: linear-gradient(90deg, var(--rule), transparent); }
</style>
</head>
<body>

  <section class="card card--contact">
    <div class="watermark-area" role="img" aria-label="Large brand watermark area in teal and light grey"></div>
    <div class="contact-block">
      <div class="contact-name">MARCUS DELANEY</div>
      <div class="contact-role">CEO/FOUNDER</div>
      <div class="contact-address">2140 Harbourview Road<br>Halifax, Nova Scotia B3H 1Y6</div>
      <div class="contact-line">902 555 0148
        <svg viewBox="0 0 12 12" aria-hidden="true"><path d="M2 1h2.5l1 3-1.5 1a6 6 0 0 0 3 3l1-1.5 3 1V10a1 1 0 0 1-1 1A9 9 0 0 1 1 2a1 1 0 0 1 1-1z" fill="#23b9bd"/></svg>
      </div>
      <div class="contact-line">902 555 0172
        <svg viewBox="0 0 12 12" aria-hidden="true"><rect x="3" y="0.5" width="6" height="11" rx="1" fill="none" stroke="#23b9bd" stroke-width="1.2"/><circle cx="6" cy="9.5" r="0.7" fill="#23b9bd"/></svg>
      </div>
      <div class="contact-line">902 555 0193
        <svg viewBox="0 0 12 12" aria-hidden="true"><rect x="1" y="4" width="10" height="6" rx="1" fill="#23b9bd"/><rect x="3" y="1" width="6" height="3" fill="#23b9bd"/></svg>
      </div>
      <div class="contact-line">hello@thebrightwayhaus.ca
        <svg viewBox="0 0 12 12" aria-hidden="true"><rect x="0.5" y="2" width="11" height="8" rx="1" fill="#23b9bd"/><path d="M1 3l5 4 5-4" fill="none" stroke="#1d2a5e" stroke-width="1"/></svg>
      </div>
      <div class="contact-line">www.thebrightwayhaus.ca
        <svg viewBox="0 0 12 12" aria-hidden="true"><circle cx="6" cy="6" r="5.5" fill="#23b9bd"/><path d="M0.5 6h11M6 0.5c-2.5 3-2.5 8 0 11M6 0.5c2.5 3 2.5 8 0 11" fill="none" stroke="#1d2a5e" stroke-width="0.8"/></svg>
      </div>
    </div>
  </section>

  <section class="card card--brand">
    <div class="brand-lockup">
      <div class="brand-mark"></div>
      <div class="brand-name">BRIGHTWAY HAUS INC.</div>
    </div>
    <div class="tagline">
      <span class="tagline-rule"></span>
      <span>Where Shine Counts</span>
      <span class="tagline-rule tagline-rule--end"></span>
    </div>
  </section>

</body>
</html>
```